Velvet Riot Rising Line of Sparkling Wine & Spirits

Back info: Nora Beth Quill Owner 555-318-4402 1480 E. Harlow Ave, Bldg. 2, & 3, Fairhollow Ca. 95871
Sparkling Wines & Memorabilia www.velvetriotrising.com
Ok I have uploaded the winning design. The color that I am after is the Fushia, Raspberry, Red, Matte Satin Matalic Finish. With a 24 Karet Gold color Foil. The Bottle is on the top row and it's the 2nd Bottle in. That is the Color that I want. This is the style of font. Make sure that you put what we're advertising. Good Luck to you all. Warmest regards, Nora
21 & up UniSex
Sparkling Wine and Memorabilia
there listed up above.....

```html
<!DOCTYPE html>
<html lang="en">
<head>
<meta charset="utf-8">
<title>Velvet Riot Rising – Business Card</title>
<link href="https://fonts.googleapis.com/css2?family=Arimo:wght@400;700&display=swap" rel="stylesheet">
<style>
  :root {
    --page-bg: #e4e4e4;
    --card-white: #ffffff;
    --fuchsia-bright: #e8229a;
    --fuchsia-mid: #c01a78;
    --raspberry-deep: #8a1248;
    --gold: #f2c766;
    --bronze: #7a4a1c;
    --bronze-light: #c08a3c;
    --ink: #1a1a1a;
    --text-white: #ffffff;
    --grey-deep: #6e6e6e;
  }
  * { margin: 0; padding: 0; box-sizing: border-box; }
  html, body {
    width: 1200px; height: 1200px; overflow: hidden;
    background: var(--page-bg);
    font-family: "Arimo", Arial, sans-serif;
  }
  .card {
    position: absolute;
    width: 688px;
    height: 393px;
    background: var(--card-white);
    overflow: hidden;
  }
  .card--front { top: 158px; left: 266px; }
  .card--back { top: 654px; left: 262px; }

  /* front */
  .bottle-art {
    position: absolute;
    border-radius: 10px 10px 8px 8px;
    background: linear-gradient(90deg, var(--raspberry-deep) 0%, var(--fuchsia-bright) 45%, var(--fuchsia-mid) 100%);
  }
  .card--front .bottle-art { left: 130px; top: 71px; width: 76px; height: 242px; }
  .divider {
    position: absolute; left: 316px; top: 0; width: 9px; height: 100%;
    background: linear-gradient(90deg, var(--bronze) 0%, var(--bronze-light) 50%, var(--bronze) 100%);
  }
  .contact-panel {
    position: absolute; left: 325px; top: 0; right: 0; bottom: 0;
    background: radial-gradient(ellipse at 45% 40%, var(--fuchsia-bright) 0%, var(--fuchsia-mid) 45%, var(--raspberry-deep) 100%);
    box-shadow: inset 0 0 0 6px rgba(120, 10, 60, 0.35);
  }
  .contact-name {
    position: absolute; left: 39px; top: 100px;
    font-size: 27px; font-weight: 700; color: var(--gold);
    letter-spacing: 0.3px; text-transform: uppercase; white-space: nowrap;
  }
  .contact-title {
    position: absolute; left: 39px; top: 130px;
    font-size: 17px; color: var(--text-white);
  }
  .contact-address {
    position: absolute; left: 39px; top: 178px;
    font-size: 16.5px; line-height: 21px; color: var(--text-white); white-space: nowrap;
  }
  .contact-lines {
    position: absolute; left: 39px; top: 254px;
    list-style: none; font-size: 16.5px; color: var(--text-white);
  }
  .contact-lines li { display: flex; align-items: center; gap: 10px; height: 21px; white-space: nowrap; }
  .contact-lines svg { width: 15px; height: 15px; flex: none; }

  /* back */
  .card--back {
    background: linear-gradient(180deg, var(--card-white) 0%, var(--card-white) 48%, #f4f4f4 58%, #b8b8b8 78%, var(--grey-deep) 100%);
  }
  .card--back .bottle-art { left: 309px; top: 57px; width: 70px; height: 243px; }
  .shelf-line {
    position: absolute; left: 145px; top: 299px; width: 407px; height: 1px;
    background: linear-gradient(90deg, transparent, #444 20%, #444 80%, transparent);
  }
  .tagline {
    position: absolute; left: 0; right: 0; top: 330px;
    text-align: center; font-size: 17px; letter-spacing: 4.2px;
    color: var(--ink); text-transform: uppercase;
  }
  .tagline strong { font-weight: 700; }
</style>
</head>
<body>
  <section class="card card--front">
    <div class="bottle-art" role="img" aria-label="Illustration of a fuchsia sparkling wine bottle with gold foil neck and brand label"></div>
    <div class="divider"></div>
    <div class="contact-panel">
      <h1 class="contact-name">Nora Beth Quill</h1>
      <p class="contact-title">Owner</p>
      <p class="contact-address">E. Harlow Ave<br>Bldg. 2, &amp; 3, Fairhollow Ca. 95871</p>
      <ul class="contact-lines">
        <li>
          <svg viewBox="0 0 16 16" aria-hidden="true"><path fill="#f2c766" d="M3.6 1.2l2.3 2.6-1.1 1.8c.9 2 2.4 3.6 4.5 4.6l1.8-1.1 2.6 2.3-1.3 2.4C7.2 13.5 2.4 8.7 1.2 3.4z"/></svg>
          <span>555-318-4402 1480</span>
        </li>
        <li>
          <svg viewBox="0 0 16 16" aria-hidden="true"><circle cx="8" cy="8" r="6.5" fill="none" stroke="#f2c766" stroke-width="1.6"/><path d="M1.8 8h12.4M8 1.5c-2.5 3.5-2.5 9.5 0 13M8 1.5c2.5 3.5 2.5 9.5 0 13" fill="none" stroke="#f2c766" stroke-width="1.2"/></svg>
          <span>www.velvetriotrising.com</span>
        </li>
      </ul>
    </div>
  </section>

  <section class="card card--back">
    <div class="bottle-art" role="img" aria-label="Illustration of a fuchsia sparkling wine bottle with gold foil neck and brand label"></div>
    <div class="shelf-line"></div>
    <p class="tagline">Sparkling <strong>Wines &amp; Memorabilia</strong></p>
  </section>
</body>
</html>
```